Maple Lantern Productions web site

I need to build a website for a new company I am launching next month. Maple Lantern Productions is a company based in New England that provides sound, lighting, and audio visual services to weddings, corporate, and any other cusomer base looking for quality service for a fair price. Looking for somebody to do a full site not just the image files. I am looking to keep the colors of my logo (orange and black) and possibly grey and white. I am looking to build my site very similar to brightvaleevents.example, which is owned by a friend of mine. I like how he has the big pictures that load in to the site and the basic menu items. I'll need a gallery of photos. The designs should communicate quality, value and trust.
My website address is maplelanternco.example.
Updates

Hi and thanks to everyone for posting such great ideas for our new design.I have some items that I'd like to ask you all to focus on in your revisions.I like how http://www.brightvaleevents.example/ website has five or six high res pictures that change in a slideshow format with a caption that loads in for each one for the different types of services. Try and capture pics like these and with teh same headings as he has. The basic menu designs have been interesting.I am more fond of the menus that are more white with some orange as I dont want it to be too dark. I'm curious to see how your galleries will work and if i'll be able to edit the pages myself? I have some more info on the company for you to fill in:website address is ciderhouseco.comemail: info@ciderhouseco.comaddress: Maple Lantern Productions57 Littlefield StreetAvon, MA 02417"New England's finest DJ's, lighting and sound, video and more. Creating memories one perfect event at a time."Put this under the loading pictures as a tagline.About Cider HouseCider House Productions is a collection of New England's finest talent, ready to make your next event the one you've dreamed of. We have the skills and expertise to deliver your vision of your perfect event. From elegant weddings to themed mitzvah's, corporate av, videography and detail lighting, we offer all of the elements to make your event a success. Added Wednesday, March 1, 2017

Designer's Please also make sure that your design flows well on any device it is being viewed on as well. Thanks. Added Wednesday, March 1, 2017

Project Deadline Extended Reason: Hello designerThank you all very much for your hard work on our project. Im sorry but i need to extend the date of my project. Our parent conpany Rook Nine Prodactions sponsors Bay Youth Assemblies and we are currently at their leadership conference on the Cape. I will be back in on Monday and with your help will get this finished by Thursday the 16th. Thanks Added Thursday, March 9, 2017

Project Deadline Extended Reason: One of the designers is not responding so I now have to make revisions with other designers. I hope to get this website done over the weekends so please get your revisions as soon as possible. Thank you. I am also upgrading the budget another $75 to hopefully get some more interest on my project. Added Wednesday, March 15, 2017

Target Market(s)

Wedding - Corporate -

Industry/Entity Type

It Company

Coding

Coded - Design and coding required

Number of Pages Required

5+ page

Font styles to use
Sans Serif

Requirements
Must have
• Photo Gallery - I want to be able to edit it myself
Nice to have
• I like the look of my friends website brightvaleevents.example

```html
<!DOCTYPE html>
<html lang="en">
<head>
<meta charset="utf-8">
<title>Maple Lantern Productions</title>
<link href="https://fonts.googleapis.com/css2?family=Open+Sans:wght@400;600;700&display=swap" rel="stylesheet">
<style>
:root{
  --orange:#f47b20;
  --orange-dark:#d9650f;
  --ink:#2b2b2b;
  --text:#6b6b6b;
  --muted:#9a9a9a;
  --line:#e4e4e4;
  --white:#ffffff;
  --dark:#1c1c22;
  --soft:#f4f4f4;
}
*{box-sizing:border-box;margin:0;padding:0}
html,body{width:1200px;height:2836px;overflow:hidden}
body{font-family:"Open Sans",Arial,sans-serif;color:var(--text);background:var(--white)}
section,header,footer{position:relative;width:1200px;overflow:hidden}
.section-title{font-size:30px;font-weight:400;color:var(--ink);text-align:center}
.title-rule{width:60px;height:2px;background:var(--orange);margin:12px auto 0}

/* Hero */
.hero{height:390px}
.hero-photo{position:absolute;inset:0;background:radial-gradient(ellipse at 50% 30%,#b89a8a 0%,#6a4f4c 35%,#2c2330 75%,#17141b 100%)}
.hero-shade{position:absolute;inset:0;background:linear-gradient(180deg,rgba(0,0,0,.35) 0%,rgba(0,0,0,.1) 40%,rgba(0,0,0,.45) 100%)}
.nav{position:absolute;top:0;left:0;right:0;height:56px;display:flex;align-items:center;justify-content:space-between;padding:0 150px 0 250px}
.brand{display:flex;align-items:center;gap:8px;font-size:15px;font-weight:700;color:var(--white)}
.brand-mark{width:14px;height:14px;background:var(--orange)}
.menu{display:flex;list-style:none;height:56px}
.menu li{display:flex;align-items:center;padding:0 14px;font-size:11px;font-weight:600;color:var(--white);text-transform:uppercase}
.menu li.active{background:var(--orange)}
.hero-copy{position:absolute;top:222px;left:0;right:0;text-align:center;color:var(--white);font-size:16px;line-height:22px;font-weight:600}
.hero-copy span{background:rgba(0,0,0,.35);padding:2px 8px}
.availability{position:absolute;top:288px;left:262px;display:flex;gap:14px}
.field{width:150px;height:26px;background:var(--white);border:1px solid var(--line);font-size:10px;color:var(--muted);display:flex;align-items:center;justify-content:space-between;padding:0 8px}
.field svg{width:8px;height:8px}
.check-btn{width:148px;height:26px;background:var(--orange);color:var(--white);font-size:10px;font-weight:600;display:flex;align-items:center;justify-content:center}

/* Intro */
.intro{height:200px;text-align:center}
.intro h1{font-size:30px;font-weight:400;color:var(--ink);padding-top:20px}
.intro p{width:800px;margin:22px auto 0;font-size:11px;line-height:18px;color:var(--muted)}
.btn-outline{display:inline-block;margin-top:22px;padding:7px 18px;border:1px solid #bdbdbd;font-size:10px;color:var(--text)}

/* Services */
.services{height:330px;background:linear-gradient(180deg,#2a2a2e,#1b1b20)}
.services-photo{position:absolute;inset:0;background:radial-gradient(ellipse at 30% 40%,#4a3b35 0%,#25232a 60%,#19181d 100%);opacity:.9}
.services .section-title{position:relative;color:var(--white);padding-top:50px}
.service-row{position:relative;display:flex;justify-content:center;gap:40px;margin-top:38px}
.service{width:160px;text-align:center;color:#cfcfcf}
.service-icon{width:46px;height:46px;margin:0 auto;border:1px solid rgba(255,255,255,.5);border-radius:50%;display:flex;align-items:center;justify-content:center}
.service-icon svg{width:20px;height:20px}
.service h3{font-size:12px;font-weight:600;color:var(--white);margin-top:10px}
.service p{font-size:9px;line-height:14px;margin-top:6px}

/* Recent work */
.recent{height:780px}
.recent .section-title{padding-top:90px}
.work-grid{position:absolute;top:165px;left:248px;width:704px;display:grid;grid-template-columns:repeat(3,224px);column-gap:16px;row-gap:20px}
.work-card{height:265px;border:1px solid var(--line);background:var(--white)}
.work-photo{height:165px}
.work-card h3{font-size:15px;font-weight:400;color:var(--orange);text-align:center;margin-top:14px}
.work-card p{font-size:8px;line-height:12px;color:var(--muted);text-align:center;padding:6px 14px 0}
.work-links{display:flex;justify-content:space-between;border-top:1px solid var(--line);margin:10px 10px 0;padding-top:8px;font-size:9px;color:var(--text)}
.work-links span::before{content:"";display:inline-block;width:6px;height:6px;background:var(--orange);margin-right:4px}
.ph-a{background:linear-gradient(135deg,#8a6a5a,#3d3440)}
.ph-b{background:linear-gradient(135deg,#e8d9cc,#9a8274)}
.ph-c{background:linear-gradient(135deg,#d8a24a,#a4552e)}
.ph-d{background:linear-gradient(135deg,#3a3f8a,#14162e)}
.ph-e{background:linear-gradient(135deg,#c9a48a,#5e4a45)}
.ph-f{background:linear-gradient(135deg,#e46a5a,#f2c34b)}

/* Gallery */
.gallery{height:500px}
.gallery .section-title{padding-top:30px}
.filters{display:flex;justify-content:center;margin-top:22px}
.filters span{font-size:8px;color:var(--text);border:1px solid var(--line);padding:4px 8px;margin-left:-1px}
.filters span.on{background:var(--orange);color:var(--white);border-color:var(--orange)}
.gallery-grid{position:absolute;top:130px;left:248px;width:704px;display:grid;grid-template-columns:repeat(4,168px);gap:10px 10.6px}
.gallery-grid div{height:170px}
.g1{background:linear-gradient(135deg,#6d5ab0,#20183f)}
.g2{background:linear-gradient(135deg,#c46a3c,#5a3022)}
.g3{background:linear-gradient(135deg,#8b8378,#3e3b38)}
.g4{background:linear-gradient(135deg,#e3b57a,#8a5d38)}
.g5{background:linear-gradient(135deg,#e7e2dc,#9b8f86)}
.g6{background:linear-gradient(135deg,#6e5548,#2b2222)}
.g7{background:linear-gradient(135deg,#b08a6e,#473a35)}
.g8{background:linear-gradient(135deg,#f0ece6,#b6a89c)}

/* Testimonial */
.testimonial{height:290px;text-align:center}
.testimonial-photo{position:absolute;inset:0;background:radial-gradient(ellipse at 60% 50%,#3b4470 0%,#1d2038 55%,#101220 100%)}
.testimonial-inner{position:relative;padding-top:30px;color:#d6d6d6}
.avatar{width:56px;height:56px;border-radius:50%;margin:0 auto;background:linear-gradient(135deg,#b48a70,#5a4236);border:2px solid var(--white)}
.stars{display:flex;justify-content:center;gap:3px;margin-top:10px}
.stars svg{width:12px;height:12px}
.testimonial blockquote{width:660px;margin:16px auto 0;font-size:11px;line-height:18px}
.testimonial cite{display:block;margin-top:12px;font-style:normal;font-size:10px;color:var(--orange)}

/* Footer */
.footer{height:346px;background:var(--white)}
.social{display:flex;justify-content:center;gap:6px;padding-top:38px}
.social span{width:18px;height:18px;background:#555}
.social span.accent{background:var(--orange)}
.footer-cols{display:flex;justify-content:center;gap:90px;margin-top:40px}
.footer-col{width:130px}
.footer-col h4{font-size:11px;font-weight:600;color:var(--orange);margin-bottom:10px}
.footer-col ul{list-style:none}
.footer-col li{font-size:9px;line-height:17px;color:var(--text)}
.copyright{position:absolute;bottom:24px;left:0;right:0;text-align:center;font-size:9px;color:var(--muted);border-top:1px solid var(--line);padding-top:14px;margin:0 250px}
</style>
</head>
<body>

<header class="hero">
  <div class="hero-photo" role="img" aria-label="Couple dancing at a wedding reception under warm lights"></div>
  <div class="hero-shade"></div>
  <nav class="nav">
    <div class="brand"><span class="brand-mark"></span>Maple Lantern</div>
    <ul class="menu">
      <li class="active">Home</li><li>About Us</li><li>Services</li><li>Gallery</li><li>Events</li><li>Contact</li>
    </ul>
  </nav>
  <div class="hero-copy">
    <span>Use the form below to check and see if your event date is available.</span><br>
    <span>We will contact you promptly if your date is available.</span>
  </div>
  <form class="availability">
    <div class="field">Event Date<svg viewBox="0 0 8 8"><path d="M0 2l4 4 4-4z" fill="#999"/></svg></div>
    <div class="field">Event Type<svg viewBox="0 0 8 8"><path d="M0 2l4 4 4-4z" fill="#999"/></svg></div>
    <div class="field">Location<svg viewBox="0 0 8 8"><path d="M0 2l4 4 4-4z" fill="#999"/></svg></div>
    <div class="check-btn">Check Availability</div>
  </form>
</header>

<section class="intro">
  <h1>Maple Lantern are Experts in All Type of Events</h1>
  <p>Maple Lantern Productions brings together skilled DJs, lighting and sound crews, and video teams ready to make your next event the one you have dreamed of. From elegant weddings to themed mitzvahs, corporate audio visual and detail lighting, we offer every element your event needs to succeed, delivered with care, fair pricing and a team you can trust on the big night.</p>
  <span class="btn-outline">Please click here see to more</span>
</section>

<section class="services">
  <div class="services-photo" role="img" aria-label="Dim party crowd with stage lights"></div>
  <h2 class="section-title">Our Services</h2>
  <div class="service-row">
    <div class="service">
      <div class="service-icon"><svg viewBox="0 0 20 20"><rect x="3" y="6" width="14" height="10" fill="none" stroke="#fff" stroke-width="1.5"/><path d="M7 6V4h6v2" fill="none" stroke="#fff" stroke-width="1.5"/></svg></div>
      <h3>Corporate Events</h3>
      <p>Sound, staging and screens for meetings, launches and galas.</p>
    </div>
    <div class="service">
      <div class="service-icon"><svg viewBox="0 0 20 20"><path d="M8 15V4l9-2v11" fill="none" stroke="#fff" stroke-width="1.5"/><circle cx="6" cy="15" r="2" fill="#fff"/><circle cx="15" cy="13" r="2" fill="#fff"/></svg></div>
      <h3>Music Concert</h3>
      <p>Full rigs, lighting and crew for live shows of any size.</p>
    </div>
    <div class="service">
      <div class="service-icon"><svg viewBox="0 0 20 20"><path d="M10 17s-7-4.5-7-9a3.5 3.5 0 0 1 7-1 3.5 3.5 0 0 1 7 1c0 4.5-7 9-7 9z" fill="none" stroke="#fff" stroke-width="1.5"/></svg></div>
      <h3>Wedding Plans</h3>
      <p>DJs, uplighting and video to shape your perfect day.</p>
    </div>
    <div class="service">
      <div class="service-icon"><svg viewBox="0 0 20 20"><path d="M2 8l8-4 8 4-8 4z" fill="none" stroke="#fff" stroke-width="1.5"/><path d="M6 10v4c2 2 6 2 8 0v-4" fill="none" stroke="#fff" stroke-width="1.5"/></svg></div>
      <h3>School and Formal Events</h3>
      <p>Proms, semi formals and dances with lights and music.</p>
    </div>
  </div>
</section>

<section class="recent">
  <h2 class="section-title">Recent Work</h2>
  <div class="title-rule"></div>
  <div class="work-grid">
    <article class="work-card"><div class="work-photo ph-a" role="img" aria-label="Audience at a corporate conference"></div><h3>Corporate Events</h3><p>Stage sound and screens for a regional leadership summit.</p><div class="work-links"><span>View Photo</span><span>Book Location</span></div></article>
    <article class="work-card"><div class="work-photo ph-b" role="img" aria-label="Wedding couple at the reception"></div><h3>Wedding Event</h3><p>Soft uplighting and a DJ set for an evening reception.</p><div class="work-links"><span>View Photo</span><span>Book Location</span></div></article>
    <article class="work-card"><div class="work-photo ph-c" role="img" aria-label="Students celebrating at a party"></div><h3>High School Party</h3><p>Dance floor lights and music for a senior celebration.</p><div class="work-links"><span>View Photo</span><span>Book Location</span></div></article>
    <article class="work-card"><div class="work-photo ph-d" role="img" aria-label="Concert crowd under blue stage lights"></div><h3>Music Concert</h3><p>Full rig and lighting for an outdoor summer show.</p><div class="work-links"><span>View Photo</span><span>Book Location</span></div></article>
    <article class="work-card"><div class="work-photo ph-e" role="img" aria-label="Guests dancing at a mitzvah celebration"></div><h3>Bar / Bat Mitzvahs</h3><p>Themed lighting and a lively DJ for family and friends.</p><div class="work-links"><span>View Photo</span><span>Book Location</span></div></article>
    <article class="work-card"><div class="work-photo ph-f" role="img" aria-label="Colourful balloons at a birthday party"></div><h3>Birthday Party</h3><p>Bright colours, music and fun for a milestone birthday.</p><div class="work-links"><span>View Photo</span><span>Book Location</span></div></article>
  </div>
</section>

<section class="gallery">
  <h2 class="section-title">Photo Gallery</h2>
  <div class="filters">
    <span class="on">All</span><span>Corporate Events</span><span>Wedding Events</span><span>School Formals</span><span>Bar / Bat Mitzvahs</span><span>Wedding Parties</span><span>High School Party</span>
  </div>
  <div class="gallery-grid">
    <div class="g1" role="img" aria-label="Party crowd under purple lights"></div>
    <div class="g2" role="img" aria-label="Guests toasting at a dinner"></div>
    <div class="g3" role="img" aria-label="Friends posing at a formal dance"></div>
    <div class="g4" role="img" aria-label="Wedding guests celebrating"></div>
    <div class="g5" role="img" aria-label="Bride and groom outdoors"></div>
    <div class="g6" role="img" aria-label="Couple at an evening event"></div>
    <div class="g7" role="img" aria-label="Group cheering at a party"></div>
    <div class="g8" role="img" aria-label="Decorated reception tables"></div>
  </div>
</section>

<section class="testimonial">
  <div class="testimonial-photo" role="img" aria-label="Crowd at a night event in blue light"></div>
  <div class="testimonial-inner">
    <div class="avatar" role="img" aria-label="Client portrait"></div>
    <div class="stars">
      <svg viewBox="0 0 12 12"><path d="M6 0l1.8 3.9 4.2.4-3.2 2.8 1 4.1L6 9.1 2.2 11.2l1-4.1L0 4.3l4.2-.4z" fill="#f47b20"/></svg>
      <svg viewBox="0 0 12 12"><path d="M6 0l1.8 3.9 4.2.4-3.2 2.8 1 4.1L6 9.1 2.2 11.2l1-4.1L0 4.3l4.2-.4z" fill="#f47b20"/></svg>
      <svg viewBox="0 0 12 12"><path d="M6 0l1.8 3.9 4.2.4-3.2 2.8 1 4.1L6 9.1 2.2 11.2l1-4.1L0 4.3l4.2-.4z" fill="#f47b20"/></svg>
      <svg viewBox="0 0 12 12"><path d="M6 0l1.8 3.9 4.2.4-3.2 2.8 1 4.1L6 9.1 2.2 11.2l1-4.1L0 4.3l4.2-.4z" fill="#f47b20"/></svg>
      <svg viewBox="0 0 12 12"><path d="M6 0l1.8 3.9 4.2.4-3.2 2.8 1 4.1L6 9.1 2.2 11.2l1-4.1L0 4.3l4.2-.4z" fill="#f47b20"/></svg>
    </div>
    <blockquote>The team handled our wedding from the first dance to the last song. The lighting was stunning, the sound was perfect and every guest kept talking about the night. We could not have asked for a more caring and professional crew at such a fair price.</blockquote>
    <cite>Laura Bennett, Wedding Client</cite>
  </div>
</section>

<footer class="footer">
  <div class="social"><span class="accent"></span><span></span><span></span><span></span><span></span></div>
  <div class="footer-cols">
    <div class="footer-col"><h4>About Us</h4><ul><li>Our Story</li><li>Our Team</li><li>Careers</li><li>Contact Us</li><li>Reviews</li></ul></div>
    <div class="footer-col"><h4>Support</h4><ul><li>Help Center</li><li>Booking Guide</li><li>Pricing</li><li>Payments</li><li>FAQs</li></ul></div>
    <div class="footer-col"><h4>Events</h4><ul><li>Weddings</li><li>Corporate</li><li>School Formals</li><li>Mitzvahs</li><li>Concerts</li></ul></div>
    <div class="footer-col"><h4>Terms &amp; Media</h4><ul><li>Terms of Use</li><li>Privacy Policy</li><li>Photo Gallery</li><li>Press</li></ul></div>
  </div>
  <p class="copyright">maplelanternco.example &middot; 2017 All Rights Reserved &middot; Privacy Policy</p>
</footer>

</body>
</html>
```